New Alcoholic Spiked Seltzer Line

We need a can design for a line of low calorie alcoholic seltzer. This product is a sparkling water and vodka drink with no sugar added in a slim 12 oz can.

This is a lighter, healthier, alternative to the sugary ready-to-drinks on the market. The product contains only 3 ingredients: Vodka, Water and Natural Flavors. It has only 100 calories but still has 5% alcohol, so you don't need to sacrifice alcohol to cut calories.

This product also does not contain any preservatives.

We want this design to communicate the following objectives to the consumer and in this order:

1. Appetizing product
2.Low calorie
3.Communicate the type of beverage (Spiked Seltzer)

The brand name of the product is VELKA.

The flavor of the product needed to be used for the design is Mango-Orange.

Comparable products are:

www.brindlefizzworks.example/
https://www.quorvabubbles.example
https://pelnavo.example/

The designs should not infringe or copy the creative directions of the products mentionned above. They are only given so that you can better understand the type of product we are developing.

Target Market(s)

Young Professional women between the ages of 25 and 44

Industry/Entity Type

Product

Colors

Designer to choose colors to be used in the design.

Requirements
Must have
• Design extendibility, meaning it can be adapted for other flavors.
• This is a new category in the market we are targeting, so consumers must easily be able to identify what type of product this is.

```html
<!DOCTYPE html>
<html lang="en">
<head>
<meta charset="UTF-8">
<title>VELKA Sparkling Water &amp; Vodka – Can Labels</title>
<link rel="stylesheet" href="https://fonts.googleapis.com/css2?family=Anton&family=Libre+Baskerville&family=Parisienne&family=Questrial&display=swap">
<style>
  :root {
    --stage: #ece6df;
    --sky-blue: #3a9fe0;
    --sky-blue-soft: #a9d6f5;
    --label-white: #fbfcfd;
    --label-silver: #e3e8ec;
    --sunset-red: #e4473a;
    --sunset-orange: #f0862c;
    --sunset-gold: #f3c23b;
    --mango: #f7a928;
    --chili: #e1372c;
    --ember: #3b2624;
    --ink-white: #ffffff;
  }
  * { box-sizing: border-box; margin: 0; padding: 0; }
  html, body {
    width: 1200px;
    height: 912px;
    overflow: hidden;
    background: var(--stage);
  }
  .canvas {
    position: relative;
    width: 1200px;
    height: 912px;
  }
  .label {
    position: absolute;
    top: 96px;
    width: 266px;
    height: 690px;
    border-radius: 16px;
    overflow: hidden;
  }
  .tagline-top,
  .tagline-bottom {
    position: absolute;
    left: 0;
    width: 100%;
    text-align: center;
    white-space: nowrap;
  }
  .tagline-top {
    top: 30px;
    font-family: "Libre Baskerville", serif;
    font-size: 13px;
    letter-spacing: 1px;
  }
  .tagline-bottom {
    bottom: 22px;
    font-family: "Questrial", sans-serif;
    font-size: 12px;
    letter-spacing: 1px;
  }

  /* ---------- Blue edition ---------- */
  .label--blue {
    left: 356px;
    background: linear-gradient(90deg, var(--label-silver) 0%, var(--label-white) 35%, var(--label-white) 65%, var(--label-silver) 100%);
  }
  .label--blue .tagline-top,
  .label--blue .tagline-bottom { color: var(--sky-blue); }
  .label--blue .tone-field {
    position: absolute;
    left: 0;
    width: 100%;
  }
  .label--blue .tone-field--top {
    top: 62px;
    height: 250px;
    background: linear-gradient(180deg, var(--sky-blue-soft) 0%, rgba(169,214,245,0.45) 45%, rgba(255,255,255,0) 100%);
  }
  .label--blue .tone-field--bottom {
    top: 430px;
    height: 230px;
    background: linear-gradient(0deg, var(--sky-blue-soft) 0%, rgba(169,214,245,0.45) 50%, rgba(255,255,255,0) 100%);
  }
  .label--blue .ribbon {
    position: absolute;
    top: 210px;
    left: -40px;
    width: 346px;
    height: 44px;
    background: var(--sky-blue);
    transform: rotate(-20deg);
    display: flex;
    align-items: center;
    justify-content: center;
    font-family: "Parisienne", cursive;
    font-size: 22px;
    color: var(--ink-white);
    white-space: nowrap;
  }
  .label--blue .brand-name {
    position: absolute;
    top: 362px;
    left: 0;
    width: 100%;
    text-align: center;
    font-family: "Questrial", sans-serif;
    font-size: 66px;
    font-weight: 400;
    line-height: 1;
    letter-spacing: 1px;
    color: var(--sky-blue);
  }

  /* ---------- Mango-Orange edition ---------- */
  .label--sunset {
    left: 733px;
    background: linear-gradient(180deg, var(--sunset-red) 0%, var(--sunset-orange) 45%, var(--sunset-gold) 100%);
  }
  .label--sunset .tagline-top,
  .label--sunset .tagline-bottom { color: var(--ink-white); }
  .label--sunset .glow-field {
    position: absolute;
    top: 40px;
    left: 0;
    width: 100%;
    height: 240px;
    background: radial-gradient(ellipse at 65% 40%, rgba(255,236,200,0.75) 0%, rgba(255,200,140,0.35) 40%, rgba(255,160,90,0) 75%);
  }
  .label--sunset .brand-name {
    position: absolute;
    top: 290px;
    left: 0;
    width: 100%;
    text-align: center;
    font-family: "Anton", sans-serif;
    font-size: 100px;
    font-weight: 400;
    line-height: 1;
    color: var(--mango);
  }
  .label--sunset .descriptor-band {
    position: absolute;
    top: 428px;
    left: 10px;
    width: 246px;
    height: 90px;
    background: var(--ember);
    transform: skewY(-4deg);
  }
  .label--sunset .descriptor {
    position: absolute;
    top: 432px;
    left: 22px;
    width: 226px;
    font-family: "Anton", sans-serif;
    font-size: 27px;
    line-height: 1.2;
    color: var(--chili);
    text-transform: uppercase;
    white-space: nowrap;
  }
  .label--sunset .descriptor span { display: block; }
  .label--sunset .descriptor span + span { padding-left: 22px; }
  .label--sunset .flavor {
    position: absolute;
    top: 548px;
    left: 0;
    width: 100%;
    text-align: center;
    font-family: "Anton", sans-serif;
    font-size: 24px;
    letter-spacing: 2px;
    color: var(--ink-white);
    text-transform: uppercase;
  }
</style>
</head>
<body>
  <main class="canvas">
    <section class="label label--blue" aria-label="VELKA blue can label">
      <div class="tone-field tone-field--top" role="img" aria-label="Blue halftone dot pattern fading downward"></div>
      <div class="tone-field tone-field--bottom" role="img" aria-label="Blue halftone dot pattern fading upward"></div>
      <p class="tagline-top">LOW CALORIE &nbsp; LOW CALORIE</p>
      <div class="ribbon">Sparkling Water &amp; Vodka</div>
      <h1 class="brand-name">VELKA</h1>
      <p class="tagline-bottom">LOW CALORIES &nbsp;5% ALC. BY VOLUME</p>
    </section>

    <section class="label label--sunset" aria-label="VELKA Mango-Orange can label">
      <div class="glow-field" role="img" aria-label="Glowing bokeh sparkles over a warm sunset sky"></div>
      <p class="tagline-top">LOW CALORIE &nbsp; LOW CALORIE</p>
      <h2 class="brand-name">VELKA</h2>
      <div class="descriptor-band"></div>
      <p class="descriptor"><span>Sparkling Water</span><span>&amp; Vodka</span></p>
      <p class="flavor">Mango-Orange</p>
      <p class="tagline-bottom">5% ALC. BY VOLUME &nbsp;100 CALORIES</p>
    </section>
  </main>
</body>
</html>
```